K SPIRES Business Card Design

Need a business card design for K Spires, we're a tower company - our main scope of work is to upgrade cellular sites: swap antennas, install new coax, fiber, replace mounts, etc. Mostly tower work.

would like to see a sharp business card design with our logo either on background or with tower image on the background - something describing our field not only in words but in images.

Target Market(s)

USA

Industry/Entity Type

Business

Contact Information for Business Card

Tarnek Obliva
Operations Manager
K Spires LLC

cell 555-318-2094
tarnek@k-spires-example.com

4185 Wexbridge Commerce Pkwy, Suite D
Norcross, GA, 30571

Requirements
Must have
• some tower related design
Nice to have
• some tower or cellular antennas on the background, if possible to compliment our logo...

```html
<!DOCTYPE html>
<html lang="en">
<head>
<meta charset="utf-8">
<title>K Spires Business Card</title>
<link href="https://fonts.googleapis.com/css2?family=Lato:wght@400;700&family=Arimo:wght@400&display=swap" rel="stylesheet">
<style>
  :root {
    --stage-light: #e8edec;
    --stage-dark: #d0dad9;
    --brand-green: #2db300;
    --brand-blue: #0000cc;
    --back-mark: #3f48e8;
    --paper: #ffffff;
    --ink-light: #ffffff;
  }
  * { margin: 0; padding: 0; box-sizing: border-box; }
  html, body { width: 1200px; height: 864px; overflow: hidden; }
  body {
    position: relative;
    background: radial-gradient(ellipse at 50% 50%, var(--stage-light) 0%, var(--stage-dark) 75%);
    font-family: "Lato", sans-serif;
  }
  .card {
    position: absolute;
    left: 341px;
    width: 518px;
    height: 305px;
    box-shadow: 0 1px 4px rgba(0,0,0,0.18);
    overflow: hidden;
  }
  .card-front { top: 96px; background: var(--paper); }
  .card-back { top: 455px; background: var(--brand-blue); }

  .contact-panel {
    position: absolute; left: 0; top: 0;
    width: 258px; height: 100%;
    background: var(--brand-green);
  }
  .name-plate {
    position: absolute; left: 0; top: 35px;
    width: 221px; height: 69px;
    background: var(--brand-blue);
    color: var(--ink-light);
    padding: 12px 0 0 27px;
  }
  .person-name { font-size: 25px; font-weight: 700; line-height: 1.1; white-space: nowrap; }
  .person-role { font-size: 15px; font-weight: 400; line-height: 1.3; }

  .contact-list {
    position: absolute; left: 27px; top: 140px;
    list-style: none;
    color: var(--ink-light);
    font-family: "Arimo", sans-serif;
    font-size: 13px;
  }
  .contact-list li {
    display: flex; align-items: flex-start;
    min-height: 22px; line-height: 17px;
    white-space: nowrap;
  }
  .contact-list .icon { width: 11px; height: 11px; margin: 3px 5px 0 0; flex: none; fill: var(--ink-light); }

  .brand-name {
    position: absolute;
    font-family: "Lato", sans-serif;
    font-weight: 700;
    white-space: nowrap;
    line-height: 1;
    text-align: center;
  }
  .brand-front { left: 258px; width: 260px; top: 122px; font-size: 48px; color: var(--brand-blue); }
  .brand-back { left: 0; width: 100%; top: 108px; font-size: 80px; color: var(--back-mark); }
</style>
</head>
<body>
  <section class="card card-front">
    <div class="contact-panel">
      <div class="name-plate">
        <div class="person-name">Tarnek Obliva</div>
        <div class="person-role">Operations Manager</div>
      </div>
      <ul class="contact-list">
        <li>
          <svg class="icon" viewBox="0 0 12 12"><path d="M3 0h6v12H3z M4 1.5v8h4v-8z"/></svg>
          555-318-2094
        </li>
        <li>
          <svg class="icon" viewBox="0 0 12 12"><path d="M1 3h10v7H1z"/><path d="M1 3l5 4 5-4" stroke="#2db300" fill="none"/></svg>
          tarnek@k-spires-example.com
        </li>
        <li>
          <svg class="icon" viewBox="0 0 12 12"><path d="M2 8l3-3 1 1-3 3z M6 4l3-3 1 1-3 3z M4 7l3-3 1 1-3 3z"/></svg>
          K Spires LLC
        </li>
        <li>
          <svg class="icon" viewBox="0 0 12 12"><path d="M6 0a4 4 0 0 1 4 4c0 3-4 8-4 8S2 7 2 4a4 4 0 0 1 4-4z M6 2.5a1.5 1.5 0 1 0 0 3 1.5 1.5 0 0 0 0-3z"/></svg>
          <span>4185 Wexbridge Commerce Pkwy,<br>Suite D, Norcross, GA, 30571</span>
        </li>
      </ul>
    </div>
    <div class="brand-name brand-front">K Spires</div>
  </section>

  <section class="card card-back">
    <div class="brand-name brand-back">K Spires</div>
  </section>
</body>
</html>
```